New Business Card Design Project

I need a design for business cards, i am an electrical business called "Corvane Electrical and Communications" i need the cards to be double sided with the company logo on the back (attached) the front needs to say my company name, web site, email address, telephone number, and ABN number and electrical license number. I am open to different arrangements of the information but would like the background to be incorporating something electrical or something that looks smart. open to all additional ideas also.

The company colours are orange and grey see logo attached.

Business Name: Corvane Electrical and Communications
Website: corvaneelectricalandcomms.example.com.au
Email: brent@corvaneelectricalandcomms.example.com.au
Telephone(mobile): 0481209736
ABN: 71208349162
Lic No: 418273D

Target Market(s)

Business entities, Project Managers, Accounts, Clients

Industry/Entity Type

Electrician

Contact Information for Business Card

I need a design for business cards, i am an electrical business called "Corvane Electrical and Communications" i need the cards to be double sided with the company logo on the back (attached) the front needs to say my company name

Font styles to use
Serif
Sans Serif

Colors
f37122
5c5c5c

Requirements
Must have
• Must have the Logo on the back open to different ways of it being on the back but had in mind to keep it central but again open to other options
Nice to have
• A real modern cool background that is eye catching yet contemporary
Should not have
• No backgrounds of a light bulb or plug or anything like that

```html
<!DOCTYPE html>
<html lang="en">
<head>
<meta charset="utf-8">
<title>Corvane Electrical and Communications – Business Cards</title>
<link href="https://fonts.googleapis.com/css2?family=Open+Sans:wght@400;600;700&display=swap" rel="stylesheet">
<style>
  :root {
    --orange: #f6a81c;
    --orange-deep: #f37122;
    --ink: #0b0b0b;
    --grey: #5c5c5c;
    --paper: #f4f2f1;
    --stage: #e6e3e1;
    --white: #ffffff;
  }
  * { margin: 0; padding: 0; box-sizing: border-box; }
  html, body { width: 1200px; height: 900px; overflow: hidden; }
  body {
    background: var(--stage);
    font-family: "Open Sans", Arial, sans-serif;
    position: relative;
  }
  .card {
    position: absolute;
    width: 556px;
    height: 344px;
    overflow: hidden;
    box-shadow: 0 6px 18px rgba(0,0,0,0.18);
  }
  .card--front { left: 238px; top: 62px; }
  .card--back  { left: 457px; top: 518px; width: 560px; }
  .card__top {
    height: 185px;
    background: var(--paper);
    position: relative;
  }
  .card__band {
    height: 159px;
    background: var(--ink);
    position: relative;
  }
  .card--back .card__top { height: 187px; }
  .card--back .card__band { height: 157px; }

  .brand-name {
    position: absolute;
    left: 0; right: 0;
    top: 78px;
    text-align: center;
    font-weight: 700;
    color: var(--grey);
    font-size: 15px;
    line-height: 1.15;
    letter-spacing: 0.5px;
  }
  .brand-name__main { display: block; font-size: 50px; letter-spacing: 2px; }

  .brand-name--faint {
    top: 64px;
    color: var(--grey);
    opacity: 0.35;
    transform: scaleX(-1);
  }

  .holder {
    position: absolute;
    right: 336px;
    top: 34px;
    text-align: right;
    color: var(--orange);
  }
  .holder__name { font-size: 18px; font-weight: 600; line-height: 24px; }
  .holder__role { font-size: 14px; color: var(--white); line-height: 18px; margin-bottom: 8px; }
  .holder__reg { font-size: 14px; font-weight: 600; line-height: 22px; }
  .holder__reg span { font-weight: 400; }

  .contacts {
    position: absolute;
    left: 242px;
    top: 50px;
    list-style: none;
    color: var(--orange);
    font-size: 11.5px;
  }
  .contacts li {
    display: flex;
    align-items: center;
    height: 20px;
  }
  .contacts svg { width: 11px; height: 11px; margin-right: 8px; fill: var(--orange); flex: none; }

  .band-art {
    position: absolute;
    inset: 0;
    background: linear-gradient(100deg, var(--ink) 0%, #2a1a05 40%, rgba(246,168,28,0.55) 70%, #2a1a05 100%);
  }
</style>
</head>
<body>

  <section class="card card--front">
    <div class="card__top">
      <div class="brand-name">
        <span class="brand-name__main">CORVANE</span>
        ELECTRICAL &amp; COMMUNICATIONS
      </div>
    </div>
    <div class="card__band">
      <div class="holder">
        <p class="holder__name">Daniel Hart</p>
        <p class="holder__role">Director</p>
        <p class="holder__reg">ABN: <span>71208349162</span></p>
        <p class="holder__reg">Lic No: <span>418273D</span></p>
      </div>
      <ul class="contacts">
        <li>
          <svg viewBox="0 0 24 24" aria-hidden="true"><path d="M6.6 10.8a15.5 15.5 0 0 0 6.6 6.6l2.2-2.2c.3-.3.7-.4 1-.2 1.1.4 2.3.6 3.6.6.6 0 1 .4 1 1V20c0 .6-.4 1-1 1A17 17 0 0 1 3 4c0-.6.4-1 1-1h3.5c.6 0 1 .4 1 1 0 1.3.2 2.5.6 3.6.1.3 0 .7-.2 1z"/></svg>
          0481209736
        </li>
        <li>
          <svg viewBox="0 0 24 24" aria-hidden="true"><path d="M2 5h20v14H2z M2 5l10 8 10-8" fill="var(--orange)" stroke="var(--ink)" stroke-width="1.5"/></svg>
          brent@corvaneelectricalandcomms.example.com.au
        </li>
        <li>
          <svg viewBox="0 0 24 24" aria-hidden="true"><circle cx="12" cy="12" r="10"/><path d="M2 12h20M12 2c3 3 3 17 0 20M12 2c-3 3-3 17 0 20" fill="none" stroke="var(--ink)" stroke-width="1.5"/></svg>
          corvaneelectricalandcomms.example.com.au
        </li>
      </ul>
    </div>
  </section>

  <section class="card card--back">
    <div class="card__top">
      <div class="brand-name brand-name--faint">
        <span class="brand-name__main">CORVANE</span>
        ELECTRICAL &amp; COMMUNICATIONS
      </div>
    </div>
    <div class="card__band">
      <div class="band-art" role="img" aria-label="Orange flowing cable wave graphic across the black band"></div>
    </div>
  </section>

</body>
</html>
```